Media Services Start-up -- Corporate Website and Logo Design. Inspiration required!

We need a logo design and corporate website design, including coding, for our start-up business.
Vennatra’s value proposition is based on bringing together media content from a vast number of geographies globally, adding human and AI curation, translation and editing, and delivering the content using tailored customer interfaces. On the one hand, the business brings together media coverage from all over the world, and on the other it brings together content, human skills and technology to deliver a supreme customer experience.
Vennatra is a B2B media monitoring and analytics business with emphasis on global customers. Vennatra's service offering is centred around sourcing media content from different markets, processing, storing and delivering the content and insights derived from it using an online platform / mobile app.
The messaging we want to create through the logo is:
- Global scope
- Speed of delivery
- Cost-efficiency
- Multi-lingual
- Tailor-made
- Trustworthy
Target Market(s)
Business to business, PR / Communications, Media, Marketing
Logo Text
Vennatra
Coding
Coded - Design and coding required
Number of Pages Required
5+ page
Font styles to use
Other font styles liked:
- See Design Brief for details
Colors
Designer to choose colors to be used in the design.

```html
<!DOCTYPE html>
<html lang="en">
<head>
<meta charset="utf-8">
<title>Vennatra – Global Media Intelligence</title>
<link href="https://fonts.googleapis.com/css2?family=Roboto:wght@400;500;700;900&display=swap" rel="stylesheet">
<style>
  :root {
    --navy: #0d3a5a;
    --navy-deep: #08304c;
    --navy-light: #134a70;
    --orange: #ff6b35;
    --page-bg: #ffffff;
    --panel-bg: #f3f3f3;
    --bar-bg: #f7f7f7;
    --text: #333a40;
    --white: #ffffff;
  }
  * { box-sizing: border-box; margin: 0; padding: 0; }
  html, body {
    width: 1200px; height: 3033px; overflow: hidden;
    background: var(--page-bg);
    font-family: 'Roboto', Arial, sans-serif;
    color: var(--text);
  }
  .screen {
    position: absolute; left: 94px; width: 1007px;
    background: var(--panel-bg);
    box-shadow: 0 4px 18px rgba(0,0,0,0.12);
    overflow: hidden;
  }
  .screen--home { top: 82px; height: 610px; }
  .screen--solutions { top: 755px; height: 2182px; }

  /* header */
  .site-header { height: 67px; background: var(--bar-bg); position: relative; }
  .brand {
    position: absolute; left: 121px; top: 0; height: 67px;
    display: flex; align-items: center; gap: 9px;
    font-weight: 700; font-size: 28px; color: var(--navy); letter-spacing: -0.3px;
  }
  .brand-dot { width: 36px; height: 36px; border-radius: 50%; background: var(--navy); }
  .main-nav {
    position: absolute; right: 121px; top: 0; height: 67px;
    display: flex; align-items: center; gap: 29px;
    font-size: 13px; font-weight: 500; color: #222;
    list-style: none;
  }
  .main-nav .is-active { color: var(--orange); }

  /* home hero */
  .hero {
    position: absolute; top: 67px; left: 0; width: 100%; height: 486px;
    background: linear-gradient(135deg, var(--navy-light) 0%, var(--navy) 40%, var(--navy-deep) 75%, var(--navy) 100%);
    color: var(--white);
  }
  .hero-title {
    position: absolute; left: 121px; top: 199px;
    font-size: 40px; font-weight: 700; line-height: 47px; letter-spacing: 0.2px;
  }
  .hero-lead {
    position: absolute; left: 122px; top: 312px; width: 420px;
    font-size: 13px; line-height: 23.5px;
  }
  .lead-form {
    position: absolute; left: 578px; top: 83px; width: 308px; height: 320px;
    background: var(--orange); text-align: center; padding-top: 30px;
  }
  .lead-form-kicker { font-size: 18px; font-weight: 500; }
  .lead-form-name { font-size: 26px; font-weight: 700; margin-top: 4px; }
  .lead-form-rule { width: 30px; height: 2px; background: var(--white); margin: 12px auto 21px; }
  .field {
    display: block; width: 257px; height: 33px; margin: 0 auto 10px;
    background: var(--white); border: 1px solid #e6e6e6;
    font: 400 13px 'Roboto', Arial, sans-serif; color: #222;
    padding-left: 15px; text-align: left; line-height: 31px;
  }
  .form-submit {
    display: block; width: 257px; height: 33px; margin: 0 auto;
    background: var(--navy); color: var(--white); border: 0;
    font: 500 14px 'Roboto', Arial, sans-serif;
  }

  /* footer */
  .site-footer {
    position: absolute; left: 0; bottom: 0; width: 100%;
    display: flex; align-items: center; justify-content: center;
    font-size: 11px;
  }
  .site-footer--light { height: 57px; background: var(--bar-bg); color: #444; }
  .site-footer--accent { height: 45px; background: var(--orange); color: var(--white); }

  /* solutions page */
  .page-banner {
    position: absolute; top: 67px; left: 0; width: 100%; height: 219px;
    background: linear-gradient(135deg, var(--navy-light) 0%, var(--navy) 45%, var(--navy-deep) 100%);
    display: flex; align-items: center; justify-content: center;
    color: var(--white); font-size: 57px; font-weight: 700; letter-spacing: 0.5px;
  }
  .solutions { position: absolute; top: 286px; left: 0; width: 100%; height: 1851px; }
  .photo {
    position: absolute; width: 250px; height: 250px; border-radius: 50%;
  }
  .service { position: absolute; width: 450px; }
  .service-title {
    font-size: 25px; font-weight: 500; color: var(--navy); letter-spacing: 0.1px;
    margin-bottom: 18px; white-space: nowrap;
  }
  .service-intro { font-size: 12.5px; line-height: 23.5px; color: #333; margin-bottom: 9px; }
  .service-intro--small { font-size: 11.5px; }
  .service-list { list-style: none; font-size: 11px; line-height: 19px; color: #444; }
  .service-list li { position: relative; padding-left: 16px; margin-bottom: 18.5px; }
  .service-list li::before {
    content: "›"; position: absolute; left: 0; top: 4px;
    width: 10px; height: 10px; border-radius: 50%;
    background: var(--orange); color: var(--white);
    font-size: 10px; line-height: 9px; text-align: center; font-weight: 700;
  }
</style>
</head>
<body>

<!-- Home -->
<section class="screen screen--home">
  <header class="site-header">
    <div class="brand"><span class="brand-dot"></span>VENNATRA</div>
    <ul class="main-nav">
      <li class="is-active">HOME</li><li>SOLUTIONS</li><li>HOW WE DO IT</li><li>OUR PEOPLE</li><li>OUR TECHNOLOGY</li>
    </ul>
  </header>
  <div class="hero">
    <h1 class="hero-title">DELIVERING GLOBAL<br>MEDIA INTELLIGENCE</h1>
    <p class="hero-lead">Vennatra is an international media intelligence service provider. We help communications teams build and operate truly global media monitoring and measurement programmes</p>
    <form class="lead-form">
      <div class="lead-form-kicker">LEARN MORE ABOUT</div>
      <div class="lead-form-name">VENNATRA</div>
      <div class="lead-form-rule"></div>
      <div class="field">Name</div>
      <div class="field">Email</div>
      <div class="field">Phone</div>
      <button type="button" class="form-submit">GET STARTED</button>
    </form>
  </div>
  <footer class="site-footer site-footer--light">©2019 Vennatra.All Rights Reserved. Privacy Policy &nbsp;|&nbsp; Terms and use</footer>
</section>

<!-- Solutions -->
<section class="screen screen--solutions">
  <header class="site-header">
    <div class="brand"><span class="brand-dot"></span>VENNATRA</div>
    <ul class="main-nav">
      <li>HOME</li><li class="is-active">SOLUTIONS</li><li>HOW WE DO IT</li><li>OUR PEOPLE</li><li>OUR TECHNOLOGY</li>
    </ul>
  </header>
  <div class="page-banner">SOLUTIONS</div>

  <div class="solutions">
    <div class="photo" style="left:140px;top:76px;background:radial-gradient(circle,#a48468,#5e4a3c)" role="img" aria-label="Photo of colleagues working together on laptops"></div>
    <div class="service" style="left:450px;top:78px">
      <h2 class="service-title">CONTENT SOURCING</h2>
      <p class="service-intro">We help you build a content strategy that meets your budget and coverage needs across earned media - Print, Online, TV and Radio.</p>
      <ul class="service-list">
        <li>Identify geographies and markets of interest</li>
        <li>Build target media source lists to fulfil monitoring and measurement requirements</li>
        <li>Using our transparent cost calculator, we help you with accurate budgeting<br>and choices to ensure you meet your strategy and objectives</li>
        <li>Translate and localise keyword searches and editorial instructions into effecient<br>source-/ country-/ provider-specific needs to minimise wasted content.</li>
      </ul>
    </div>

    <div class="service" style="left:118px;top:477px;width:440px">
      <h2 class="service-title">CONTENT COLLECTION</h2>
      <p class="service-intro service-intro--small">We consolidate and manage the delivery of your global media content into a<br>Cloud-based scalable media platform, taking the headache of content management<br>away from your teams.</p>
    </div>
    <div class="photo" style="left:616px;top:398px;background:radial-gradient(circle,#3a6aa8,#7a3a5a 60%,#111)" role="img" aria-label="Photo of a wall of colourful media screens"></div>

    <div class="photo" style="left:140px;top:720px;background:radial-gradient(circle,#b08a66,#6d5440)" role="img" aria-label="Overhead photo of a team working at a wooden desk with laptop and tablet"></div>
    <div class="service" style="left:450px;top:723px">
      <h2 class="service-title">CONTENT AUGMENTATION</h2>
      <ul class="service-list">
        <li>We manage and normalise all of the source-level reference data - country,<br>language, reach etc.</li>
        <li>We add editorial validation to ensure only the content required reaches your delivery,<br>removing inevitable noise from source providers</li>
        <li>Tagging - AI and human based tagging to detect locations, people, topics, products,<br>brands, services, etc.</li>
        <li>Human and automated grouping of stories across geographies - clustering,<br>"also-in" groupings etc.</li>
        <li>Translation summarisation - AI Translation or human-created depending on<br>budget, speed of delivery and need.</li>
        <li>Digest authoring - refining the essence of today's coverage into a concise<br>board-ready output for your organisation</li>
      </ul>
    </div>

    <div class="service" style="left:118px;top:1154px;width:470px">
      <h2 class="service-title">CONTENT DELIVERY</h2>
      <p class="service-intro">Early morning delivery of a consolidated, ready-to-consume media coverage</p>
      <ul class="service-list">
        <li>Customised email templates, delivering content in templates designed<br>to meet your needs</li>
        <li>Customised platform - modern portal tailored to meet your media management needs,<br>removing the unwanted clutter and focusing on the job at hand</li>
        <li>Integration with Intranets, third-party communication tools e.g. Chatwell, RSS readers,<br>customised APIs</li>
      </ul>
    </div>
    <div class="photo" style="left:616px;top:1130px;background:radial-gradient(circle,#f3c27a,#b08a70 70%,#6e7f92)" role="img" aria-label="Photo of hands holding a phone with glowing location pins"></div>

    <div class="photo" style="left:140px;top:1459px;background:radial-gradient(circle,#c9a27c,#8a8a8c 70%,#5a6070)" role="img" aria-label="Photo of a person at a laptop with a world map overlay"></div>
    <div class="service" style="left:450px;top:1450px">
      <h2 class="service-title">MEDIA INSIGHTS &amp; CONSULTANCY</h2>
      <ul class="service-list">
        <li>Levering the normalised content sets from your integrated monitoring service,<br>we can analyse and tag your coverage based on complex qualitative measurement<br>criteria, consistent across all languages and geographies, to combine with<br>quantitative metrics.</li>
        <li>Ability to create a single consistent measurement programme across all of<br>your global operations.</li>
        <li>Consultancy to HQ and local offices on how to utilise and align existing<br>measurement and insight intiatives to provide continuity.</li>
        <li>Customised online dashboards with near real time data insights, coupled with<br>Board-ready offline reporting and export options.</li>
        <li>Integration with social media content, third-party data, point-of-sale, Trafficly<br>Analytics, and delivering on your Integrated Communications Framework</li>
      </ul>
    </div>
  </div>

  <footer class="site-footer site-footer--accent">©2019 Vennatra.All Rights Reserved. Privacy Policy &nbsp;|&nbsp; Terms and use</footer>
</section>

</body>
</html>
```